Bramblewood Joinery Website

My client Bramblewood Joinery is looking for a redesign for a Word Press Website. Their current site is at www.bramblewoodjoinery.example They are a custom cabinet company, but also create bathroom, living room, bar and entertainment and bedroom cabinets too. They would like a design that emulates the master craftsman work they do yet a contemporary style.

Their current site was designed using Flash elements.

Target Market(s)

Home owners and builders of high end homes

Industry/Entity Type

Entertainment

Font styles to use
Serif
Decorative

Requirements
Must have
• Must show their work and logo using a contemporary style.
Nice to have
• Sliders that showcase their projects.

```html
<!DOCTYPE html>
<html lang="en">
<head>
<meta charset="utf-8">
<title>Bramblewood Joinery</title>
<link rel="stylesheet" href="https://fonts.googleapis.com/css2?family=Oswald:wght@500;700&family=Cabin:wght@400;600&family=Arimo:ital,wght@0,400;0,700;1,400;1,700&display=swap">
<style>
:root{
  --green:#3cb944;
  --green-dark:#2e9a36;
  --ink:#222;
  --text:#555;
  --muted:#8a8a8a;
  --dark:#262626;
  --darker:#1b1b1b;
  --grey-band:#e3e3e3;
  --line:#e1e1e1;
  --white:#fff;
}
*{margin:0;padding:0;box-sizing:border-box}
html,body{width:1200px;height:2282px;overflow:hidden}
body{position:relative;background:var(--white);font-family:"Arimo",Arial,sans-serif;color:var(--text)}

/* header */
.site-header{position:absolute;left:0;top:0;width:1200px;height:122px;border-top:4px solid var(--green)}
.brand{position:absolute;left:160px;top:16px;display:flex;align-items:center;gap:12px}
.brand-mark{width:84px;height:84px;border-radius:50%;border:4px solid var(--green)}
.brand-name{font-family:"Cabin",sans-serif;font-weight:600;font-size:22px;color:var(--green);line-height:1.1;width:150px}
.social-badge{position:absolute;left:734px;top:42px;width:146px;height:46px;border:1px solid #c9c9c9;background:#f2f2f2;display:flex;align-items:center;gap:8px;padding-left:8px;font-family:"Cabin",sans-serif;font-size:17px;line-height:1.1;color:#3a5a98}
.social-badge span.sq{width:30px;height:30px;background:#3a5a98;flex:none}
.contact-cta{position:absolute;left:902px;top:40px}
.contact-cta small{display:block;font-size:12px;color:var(--ink)}
.contact-cta strong{display:block;font-family:"Oswald",sans-serif;font-weight:500;font-size:28px;color:var(--green);letter-spacing:1px;line-height:1.2}

/* hero */
.hero-band{position:absolute;left:0;top:122px;width:1200px;height:414px;background:repeating-linear-gradient(90deg,#202020 0 7px,#2a2a2a 7px 9px,#242424 9px 15px)}
.main-nav{position:absolute;left:160px;top:148px;width:882px;height:48px;background:var(--white);display:flex;font-family:"Cabin",sans-serif;font-size:12.5px;color:var(--ink)}
.main-nav a{display:flex;align-items:center;padding:0 9.5px;border-right:1px solid #ddd;text-decoration:none;color:inherit;white-space:nowrap}
.main-nav a.active{background:var(--green);color:var(--white);font-weight:600}
.main-nav .search{margin-left:auto;width:46px;background:var(--green);display:flex;align-items:center;justify-content:center}
.slider{position:absolute;left:160px;top:196px;width:882px;height:403px;background:linear-gradient(160deg,#6b3c1c 0%,#a5642e 35%,#c98a4a 55%,#7a4a22 80%,#3f2410 100%)}
.slider-arrow{position:absolute;top:192px;width:46px;height:46px;border:3px solid rgba(255,255,255,.75);border-radius:50%;background:rgba(0,0,0,.25)}
.slider-caption{position:absolute;left:0;top:250px;width:100%;text-align:center;color:var(--white)}
.slider-caption h2{font-family:"Oswald",sans-serif;font-weight:700;font-size:38px;letter-spacing:.5px;text-shadow:0 2px 4px rgba(0,0,0,.5)}
.slider-caption p{font-size:18px;margin-top:2px;text-shadow:0 1px 3px rgba(0,0,0,.6)}
.slider-dots{position:absolute;left:0;width:100%;top:361px;display:flex;justify-content:center;gap:5px}
.slider-dots i{width:13px;height:13px;border-radius:50%;background:#ccc;border:1px solid #999}
.slider-dots i.on{background:var(--green)}

.tagline{position:absolute;left:0;top:626px;width:1200px;text-align:center;font-family:"Cabin",sans-serif;font-size:27px;line-height:32px;color:var(--ink)}
.tagline em{font-style:normal;color:var(--green)}

/* offer */
.offer{position:absolute;left:0;top:727px;width:1200px;height:302px;background:var(--green);color:var(--white);text-align:center}
.offer h3{font-family:"Cabin",sans-serif;font-weight:400;font-size:23px;margin-top:42px}
.offer-list{position:absolute;top:94px;left:160px;width:882px;display:flex;justify-content:space-between}
.offer-item{width:120px;display:flex;flex-direction:column;align-items:center;font-family:"Cabin",sans-serif;font-size:17px;white-space:nowrap}
.offer-item svg{width:56px;height:48px;margin-bottom:10px}
.offer p{position:absolute;left:180px;top:194px;width:840px;font-size:13.5px;line-height:21px;text-align:justify;text-align-last:center}

/* gallery + news */
.section-title{position:absolute;font-family:"Cabin",sans-serif;font-weight:400;font-size:22px;color:var(--ink)}
.gallery{position:absolute;left:160px;top:1117px;width:601px;display:grid;grid-template-columns:repeat(3,193px);grid-auto-rows:102px;gap:14px 11px}
.gallery div{border:2px solid #ddd}
.btn{position:absolute;height:30px;display:flex;align-items:center;justify-content:center;font-family:"Cabin",sans-serif;font-size:13.5px;color:var(--white)}
.btn-dark{background:var(--ink)}
.btn-green{background:var(--green)}
.news-item{position:absolute;left:787px;width:255px;height:56px;display:flex;gap:8px}
.news-thumb{width:52px;height:46px;background:linear-gradient(135deg,#6c6a64,#b8b2a6);flex:none;margin-top:4px}
.news-item h4{font-size:12.5px;color:var(--ink);font-weight:700}
.news-item h4.hl{color:var(--green)}
.news-item p{font-size:11px;line-height:14px;color:var(--muted);margin-top:3px}
.news-rule{position:absolute;left:787px;width:255px;height:1px;background:var(--line)}
.divider{position:absolute;left:160px;top:1430px;width:882px;height:1px;background:var(--line)}

/* clients */
.clients{position:absolute;left:160px;top:1506px;width:450px;display:grid;grid-template-columns:repeat(3,150px);grid-auto-rows:78px}
.client{display:flex;align-items:center;font-family:"Cabin",sans-serif;font-weight:600;font-size:30px;color:var(--ink);white-space:nowrap}
.avatar{position:absolute;left:628px;top:1508px;width:68px;height:68px;background:linear-gradient(160deg,#7a5a46,#c9a18a)}
.quote{position:absolute;left:715px;top:1508px;width:327px;background:var(--green);border-radius:5px;padding:12px 14px 12px 20px;color:var(--white);font-style:italic;font-weight:700;font-size:11px;line-height:15.5px;text-align:justify}
.quote:before{content:"";position:absolute;left:-10px;top:16px;border:10px solid transparent;border-left:0;border-right-color:var(--green)}
.quote-by{position:absolute;left:728px;top:1652px;font-style:italic;font-size:13px;color:var(--ink)}

/* hello */
.hello{position:absolute;left:0;top:1706px;width:1200px;height:253px;background:var(--grey-band);text-align:center}
.hello h3{font-family:"Oswald",sans-serif;font-weight:700;font-size:32px;color:var(--ink);margin-top:60px;letter-spacing:1px}
.hello p{width:840px;margin:6px auto 0;font-size:13px;line-height:19px;color:var(--muted)}
.social{display:flex;justify-content:center;gap:14px;margin-top:22px}
.social i{width:38px;height:38px;border-radius:50%;background:var(--green-dark);border:3px solid var(--white)}

/* footer */
.footer{position:absolute;left:0;top:1959px;width:1200px;height:285px;border-top:10px solid var(--green);background:repeating-linear-gradient(90deg,#232323 0 7px,#2b2b2b 7px 9px,#262626 9px 15px)}
.footer h5{position:absolute;top:48px;font-family:"Cabin",sans-serif;font-weight:600;font-size:17px;color:var(--green)}
.footer-about{position:absolute;left:164px;top:80px;width:300px;font-size:12.5px;line-height:19.5px;color:#ddd;text-align:justify}
.footer-about em{font-style:normal;color:var(--green)}
.portfolio{position:absolute;left:504px;top:86px;display:grid;grid-template-columns:repeat(4,53px);grid-auto-rows:44px;gap:11px 10px}
.portfolio div{background:linear-gradient(135deg,#5e4a3a,#b9a894);border:1px solid #555}
.footer-contact{position:absolute;left:789px;top:80px;width:260px;font-size:11.5px;line-height:16px;color:#ddd}
.footer-contact b{color:var(--green)}
.footer-contact .row{display:flex;align-items:center;gap:14px;margin-top:8px}
.footer-contact svg{width:16px;height:16px;fill:#ddd}
.bottom-bar{position:absolute;left:0;top:2244px;width:1200px;height:38px;background:var(--darker);font-size:11.5px;color:#ccc}
.bottom-bar nav{position:absolute;left:164px;top:12px}
.bottom-bar .copy{position:absolute;right:160px;top:12px}
.bottom-bar .copy b{color:var(--green);font-weight:400}
</style>
</head>
<body>

<header class="site-header">
  <div class="brand"><div class="brand-mark"></div><div class="brand-name">Bramblewood Joinery</div></div>
  <div class="social-badge"><span class="sq"></span>Find us online</div>
  <div class="contact-cta"><small>Have a Question for Us?</small><strong>555 010 4477</strong></div>
</header>

<div class="hero-band"></div>
<nav class="main-nav">
  <a class="active">HOME</a><a>WHO WE ARE</a><a>GETTING STARTED</a><a>CONTACT US</a><a>CUSTOMER EXPERIENCE</a><a>PROFESSIONAL</a><a>PORTFOLIO</a><a>CABINET HARDWARE</a>
  <span class="search"><svg width="20" height="20" viewBox="0 0 20 20"><circle cx="8" cy="8" r="6" fill="none" stroke="#fff" stroke-width="2.5"/><line x1="12.5" y1="12.5" x2="18" y2="18" stroke="#fff" stroke-width="2.5"/></svg></span>
</nav>
<section class="slider" role="img" aria-label="Photo of a warm wooden fitted kitchen with an island and hardwood floor">
  <span class="slider-arrow" style="left:12px"></span>
  <span class="slider-arrow" style="right:12px"></span>
  <div class="slider-caption"><h2>AFFORDABLE SOLUTIONS FOR LIVING</h2><p>Style, Comfort, Quality, Selection!</p></div>
  <div class="slider-dots"><i></i><i></i><i class="on"></i><i></i><i></i></div>
</section>

<p class="tagline">We’ve been <em>designing and manufacturing</em><br>the Midwest’s finest <em>custom cabinets and fixtures</em> since <em>1966</em></p>

<section class="offer">
  <h3>WHAT WE OFFER</h3>
  <div class="offer-list">
    <div class="offer-item"><svg viewBox="0 0 56 48" fill="none" stroke="#e8f6e9" stroke-width="3"><circle cx="28" cy="24" r="14"/><line x1="6" y1="10" x2="6" y2="40"/><line x1="50" y1="10" x2="50" y2="40"/></svg>KITCHEN</div>
    <div class="offer-item"><svg viewBox="0 0 56 48" fill="none" stroke="#fff" stroke-width="3"><path d="M8 24h40v6a10 10 0 0 1-10 10H18A10 10 0 0 1 8 30z"/><path d="M14 24V8h8"/></svg>BATH</div>
    <div class="offer-item"><svg viewBox="0 0 56 48" fill="none" stroke="#e8f6e9" stroke-width="3"><rect x="20" y="8" width="22" height="16"/><line x1="8" y1="30" x2="50" y2="30"/><line x1="14" y1="30" x2="14" y2="44"/><line x1="44" y1="30" x2="44" y2="44"/></svg>OFFICE</div>
    <div class="offer-item"><svg viewBox="0 0 56 48" fill="#e8f6e9"><path d="M22 4h12l-2 12 12 28H12l12-28z"/></svg>CLOSET/DRESSING</div>
    <div class="offer-item"><svg viewBox="0 0 56 48" fill="none" stroke="#e8f6e9" stroke-width="3"><circle cx="28" cy="16" r="7"/><rect x="10" y="26" width="36" height="8"/><line x1="16" y1="34" x2="16" y2="44"/><line x1="40" y1="34" x2="40" y2="44"/></svg>WORKSHOP</div>
    <div class="offer-item"><svg viewBox="0 0 56 48" fill="none" stroke="#e8f6e9" stroke-width="3"><rect x="8" y="8" width="40" height="24"/><line x1="28" y1="32" x2="28" y2="42"/><line x1="18" y1="42" x2="38" y2="42"/></svg>ENTERTAINMENT</div>
  </div>
  <p>Sed ut perspiciatis unde omnis iste natus error sit voluptatem accusantium doloremque laudantium, totam rem aperiam, eaque ipsa quae ab illo inventore veritatis et quasi architecto beatae vitae dicta sunt explicabo. Nemo sit voluptatem doloremque laudantium, totam ratione voluptatem sequi nesciunt.</p>
</section>

<h3 class="section-title" style="left:160px;top:1074px">OUR GALLERY</h3>
<div class="gallery">
  <div role="img" aria-label="White kitchen cabinets" style="background:linear-gradient(135deg,#d9d6cf,#9d9a92)"></div>
  <div role="img" aria-label="Bright kitchen with island" style="background:linear-gradient(135deg,#e6e3dc,#a8a196)"></div>
  <div role="img" aria-label="Dark media wall unit" style="background:linear-gradient(135deg,#6d6a66,#2d2b29)"></div>
  <div role="img" aria-label="Kitchen with dark island" style="background:linear-gradient(135deg,#bdb8ae,#3a3632)"></div>
  <div role="img" aria-label="Black lacquered island" style="background:linear-gradient(135deg,#7a6a58,#1f1c19)"></div>
  <div role="img" aria-label="Dark wood island in a kitchen" style="background:linear-gradient(135deg,#cfc9bf,#3b3530)"></div>
</div>
<div class="btn btn-dark" style="left:160px;top:1349px;width:129px">VIEW MORE</div>

<h3 class="section-title" style="left:787px;top:1074px">RECENT NEWS</h3>
<article class="news-item" style="top:1118px"><div class="news-thumb" role="img" aria-label="Project photo"></div><div><h4 class="hl">Morbi id malesuada augu elis</h4><p>Morbi id malesuada augue auctor aliq nunc sit amet, porttitor lobortis.</p></div></article>
<div class="news-rule" style="top:1186px"></div>
<article class="news-item" style="top:1198px"><div class="news-thumb" role="img" aria-label="Project photo"></div><div><h4>Morbi id malesuada augu elis</h4><p>Morbi id malesuada augue auctor aliq nunc sit amet, porttitor lobortis.</p></div></article>
<div class="news-rule" style="top:1266px"></div>
<article class="news-item" style="top:1282px"><div class="news-thumb" role="img" aria-label="Project photo"></div><div><h4>Morbi id malesuada augu elis</h4><p>Morbi id malesuada augue auctor aliq nunc sit amet, porttitor lobortis.</p></div></article>
<div class="btn btn-green" style="left:787px;top:1349px;width:130px">VIEW MORE</div>

<div class="divider"></div>

<h3 class="section-title" style="left:160px;top:1466px">OUR CLIENTS</h3>
<div class="clients">
  <div class="client">Marlow</div>
  <div class="client">Vellina</div>
  <div class="client">Ostra</div>
  <div class="client">Telford</div>
  <div class="client">Quenby</div>
  <div class="client">Ashcombe</div>
</div>

<h3 class="section-title" style="left:628px;top:1466px">TESTIMONIALS</h3>
<div class="avatar" role="img" aria-label="Portrait of the client giving the testimonial"></div>
<blockquote class="quote">“Lorem ipsum dolor sit amet, consectetur adipiscing elit, sed do eiusmod tempor incididunt ut labore et dolore magna aliqua. Ut enim ad minim veniam, quis nostrud exercitation ullamco laboris nisi ut aliquip ex ea commodo consequat. Duis aute irure dolor in reprehenderit in voluptate velit esse cillum dolore eu fugiat nulla. Excepteur sint cupidata”.</blockquote>
<div class="quote-by">- Nora Ellis</div>

<section class="hello">
  <h3>HELLO !</h3>
  <p>Sed ut perspiciatis unde omnis iste natus error sit voluptatem accusantium doloremque laudantium, totam rem aperiam, eaque ipsa quae e natus error sit voluptab illo inventore veritatis et quasi architecto beatae vitae dicta sunt explicabo.</p>
  <div class="social"><i></i><i></i><i></i><i></i></div>
</section>

<footer class="footer">
  <h5 style="left:164px">ABOUT US</h5>
  <p class="footer-about">Established in <em>1966</em>, <em>Bramblewood Joinery</em> has long stood as one of the Midwest’s most renowned makers of custom cabinets and fixtures. Our handcrafted, award-winning creations have been chosen by hundreds of noteworthy homebuilders. And while we custom build cabinets, we built our business around the belief that our customers absolutely, unequivocally come first.</p>
  <h5 style="left:504px">RECENT PORTFOLIO</h5>
  <div class="portfolio" role="img" aria-label="Thumbnails of recent cabinet projects">
    <div></div><div></div><div></div><div></div><div></div><div></div><div></div><div></div><div></div><div></div><div></div><div></div>
  </div>
  <h5 style="left:789px">CONTACT US</h5>
  <div class="footer-contact">
    <p>Got a question for Bramblewood? We’d love to hear from you! Whether it’s for a project inquiry.</p>
    <p><b>Bramblewood Joinery</b><br>Owen Hartley, 48 Fernhill Road, Oakdale, MO-60000</p>
    <div class="row"><svg viewBox="0 0 16 16"><path d="M3 1l3 3-2 2c1 2 3 4 5 5l2-2 3 3-2 3C6 15 1 10 0 3z"/></svg>: &nbsp;555.014.2300</div>
    <div class="row"><svg viewBox="0 0 16 16"><rect x="2" y="5" width="12" height="9"/><rect x="4" y="1" width="8" height="4"/></svg>: &nbsp;555.014.7835</div>
    <div class="row"><svg viewBox="0 0 16 16"><rect x="1" y="3" width="14" height="10"/></svg>: &nbsp;hello@bramblewoodjoinery.example</div>
  </div>
</footer>
<div class="bottom-bar">
  <nav>Home &nbsp;| &nbsp;Who Are We &nbsp;| &nbsp;Professional &nbsp;| &nbsp;Portfolio &nbsp;| &nbsp;Contact Us</nav>
  <div class="copy">© 2015. All rights reserved. <b>Bramblewood Joinery.</b></div>
</div>

</body>
</html>
```